We need a complete design for our construction company KELTO CONSTRUCTION based in Auckland New Zealand, we need a logo, website, business card, vehicle design etc..
We are a mid to high-end construction company who work mostly on residential projects and some commercial.

What we want to see in the design;
Professional,
Architectural,
Simple,
Alternative,

We want the design to communicate professionalism, high quality wormanship and and quality service.

Target Market(s)

People looking for a quality building/ construction company

Industry/Entity Type

Construction Company

Contact Information for Business Card

KELTO CONSTRUCTION.co.nz
Lino Verasek
lino@keltoconstruction.example.nz
021 5807 462

Logo Text

KELTO CONSTRUCTION

Number of Pages Required

5+ page

Font styles to use
Sans Serif

Colors

Designer to choose colors to be used in the design.

Requirements
Must have
• Must appear high end, professional, quality, be simple, easy to use, give security to potential clients
Nice to have
• high-quality photos of our recent projects
• about us page
• blog page
• contact us page
• high quality content
Should not have
• should not be hard to use and have too much going on.

```html
<!DOCTYPE html>
<html lang="en">
<head>
<meta charset="utf-8">
<title>Kelto Construction</title>
<link href="https://fonts.googleapis.com/css2?family=Raleway:wght@300;400;500;600;700&family=Open+Sans:wght@400;600;700&display=swap" rel="stylesheet">
<style>
:root{
  --blue:#1a5cc0;
  --blue-dark:#1550ac;
  --navy:#0c1526;
  --yellow:#f2c200;
  --ink:#1a1a1a;
  --text:#333;
  --band:#ebebeb;
  --tile:#ececec;
  --white:#fff;
}
*{box-sizing:border-box;margin:0;padding:0}
html,body{width:1200px;height:3010px;overflow:hidden}
body{position:relative;background:var(--white);font-family:"Open Sans",Arial,sans-serif;color:var(--text)}

/* header */
.site-header{position:absolute;left:0;top:0;width:1200px;height:96px;background:var(--white)}
.brand{position:absolute;left:104px;top:31px;font-size:28px;font-weight:400;color:var(--ink)}
.contact-chip{position:absolute;display:flex;align-items:center;gap:12px}
.chip-icon{width:34px;height:34px;border-radius:50%;background:var(--yellow);display:flex;align-items:center;justify-content:center}
.chip-email{left:702px;top:28px;font-size:13px;color:var(--ink)}
.chip-call{left:920px;top:24px}
.chip-call .lbl{font-size:13px;color:var(--ink);line-height:16px}
.chip-call .num{font-size:17px;color:var(--blue);line-height:22px}

/* nav */
.main-nav{position:absolute;left:0;top:96px;width:1200px;height:52px;background:var(--blue)}
.main-nav a{position:absolute;top:0;height:52px;line-height:52px;font-size:15px;color:var(--white);text-decoration:none}
.main-nav .active{left:90px;width:96px;text-align:center;background:#e6e6e6;color:var(--ink);border-bottom:4px solid var(--yellow);line-height:50px}
.nav-search{position:absolute;left:1064px;top:17px}

/* hero */
.hero{position:absolute;left:0;top:148px;width:1200px;height:438px;
  background:
    linear-gradient(180deg,rgba(0,0,0,0) 55%,rgba(30,40,25,.55) 100%),
    linear-gradient(180deg,#8e9aa6 0%,#6e7c8a 18%,#4f6276 32%,#5a6a78 45%,#3f4d5a 65%,#2d3a2a 100%)}
.hero-title{position:absolute;left:0;top:180px;width:1200px;text-align:center;font-family:"Raleway",sans-serif;font-weight:300;font-size:48px;color:var(--white);letter-spacing:1px}
.hero-sub{position:absolute;left:0;top:246px;width:1200px;text-align:center;font-size:16px;color:var(--white)}
.hero-arrows{position:absolute;left:556px;top:368px}

/* section headings */
.section-title{position:absolute;left:0;width:1200px;text-align:center;font-family:"Raleway",sans-serif;font-weight:300;font-size:38px;color:var(--ink);letter-spacing:.5px}
.rule{position:absolute;left:576px;width:48px;height:3px;background:var(--blue)}
.lead{position:absolute;left:80px;width:1040px;text-align:center;font-size:13.5px;line-height:26px;color:var(--text)}

/* welcome */
.welcome{position:absolute;left:0;top:586px;width:1200px;height:316px;background:var(--blue)}
.welcome .section-title{top:58px;color:var(--white)}
.welcome .rule{top:120px;background:var(--white)}
.welcome .lead{top:142px;color:var(--white)}
.btn{position:absolute;height:44px;line-height:44px;text-align:center;background:var(--ink);color:var(--white);font-size:14px;font-weight:700;letter-spacing:.5px}
.welcome .btn{left:538px;top:230px;width:124px}

/* services */
.services .section-title{top:982px}
.services .rule{top:1034px}
.services .lead{top:1062px}
.service-card{position:absolute;top:1128px;width:242px;height:180px;background:var(--tile);text-align:center}
.service-card svg{position:absolute;left:89px;top:22px}
.service-card .name{position:absolute;left:0;top:104px;width:100%;font-family:"Raleway",sans-serif;font-size:21px;font-weight:500;color:var(--ink)}
.service-card.featured{background:var(--blue)}
.service-card.featured .name{color:var(--white)}

/* projects */
.projects{position:absolute;left:0;top:1346px;width:1200px;height:766px;background:var(--band)}
.projects .section-title{top:80px}
.projects .rule{top:132px}
.projects .lead{top:160px}
.project-card{position:absolute;width:330px;height:210px}
.project-card .photo{position:absolute;left:0;top:0;width:330px;height:154px}
.project-card .label{position:absolute;left:0;top:154px;width:330px;height:56px;line-height:56px;background:var(--blue);color:var(--white);text-align:center;font-size:22px;letter-spacing:.5px}
.dots{position:absolute;left:574px;top:710px;display:flex;gap:8px}
.dots span{width:10px;height:10px;border-radius:50%;background:#777}

/* blog */
.blog .section-title{top:2152px}
.blog .rule{top:2206px}
.blog-card{position:absolute;top:2252px;width:330px}
.blog-card .photo{position:relative;width:330px;height:210px}
.date-badge{position:absolute;left:138px;top:64px;width:54px;height:80px;border:2px solid var(--white);background:rgba(20,20,20,.65);color:var(--white);text-align:center;font-size:26px;line-height:30px;padding-top:8px}
.date-badge small{display:block;font-size:20px;line-height:26px}
.blog-card p{margin-top:12px;text-align:center;font-size:13px;line-height:24px;color:var(--text);padding:0 6px}
.blog-card .btn{left:104px;top:306px;width:124px}

/* footer */
.site-footer{position:absolute;left:0;top:2700px;width:1200px;height:310px;background:var(--navy);color:var(--white)}
.foot-title{position:absolute;top:72px;font-size:19px;font-weight:600}
.foot-brand{position:absolute;left:74px;top:70px;font-size:24px;font-weight:700}
.foot-about{position:absolute;left:74px;top:110px;width:262px;font-size:12.5px;line-height:22px;color:#d8dbe2}
.foot-more{position:absolute;left:74px;top:210px;font-size:12.5px;color:var(--yellow)}
.quick a{position:absolute;font-size:13px;color:#e4e6ea;text-decoration:none;padding-left:24px}
.quick a::before{content:"";position:absolute;left:2px;top:5px;width:6px;height:6px;border-top:2px solid var(--yellow);border-right:2px solid var(--yellow);transform:rotate(45deg)}
.contact-row{position:absolute;left:636px;display:flex;align-items:flex-start;gap:14px;font-size:12.5px;line-height:22px;color:#e4e6ea}
.ring{flex:none;width:34px;height:34px;border-radius:50%;border:1px solid #4a5263;display:flex;align-items:center;justify-content:center}
.social{position:absolute;left:946px;top:116px;display:flex;gap:12px}
.social span{width:34px;height:34px;border-radius:50%;border:2px solid var(--yellow);display:flex;align-items:center;justify-content:center}
.social span::after{content:"";width:8px;height:8px;background:var(--yellow)}
.copy{position:absolute;left:946px;top:168px;font-size:12px;line-height:24px;color:#d8dbe2}
.mark{position:absolute;left:1152px;top:272px;font-size:11px;color:#c8ccd4}
</style>
</head>
<body>

<header class="site-header">
  <div class="brand">Kelto Construction</div>
  <div class="contact-chip chip-email">
    <span class="chip-icon"><svg width="16" height="12" viewBox="0 0 16 12"><rect x="0.5" y="0.5" width="15" height="11" fill="#fff"/><path d="M1 1l7 6 7-6" fill="none" stroke="#f2c200" stroke-width="1.6"/></svg></span>
    <span>info@keltosite.example</span>
  </div>
  <div class="contact-chip chip-call">
    <span class="chip-icon"><svg width="16" height="16" viewBox="0 0 24 24"><path d="M6.6 10.8a15 15 0 006.6 6.6l2.2-2.2c.3-.3.7-.4 1-.2 1.1.4 2.3.6 3.6.6.6 0 1 .4 1 1V20c0 .6-.4 1-1 1A17 17 0 013 4c0-.6.4-1 1-1h3.5c.6 0 1 .4 1 1 0 1.3.2 2.5.6 3.6.1.3 0 .7-.2 1z" fill="#fff"/></svg></span>
    <div><div class="lbl">Call Us</div><div class="num">1-800 555 0193</div></div>
  </div>
</header>

<nav class="main-nav">
  <a class="active">Home</a>
  <a style="left:208px">About Us</a>
  <a style="left:322px">Projects</a>
  <a style="left:428px">Blog</a>
  <a style="left:508px">Contact Us</a>
  <svg class="nav-search" width="18" height="18" viewBox="0 0 18 18"><circle cx="7.5" cy="7.5" r="5.5" fill="none" stroke="#fff" stroke-width="2.2"/><path d="M11.5 11.5l5 5" stroke="#fff" stroke-width="2.6"/></svg>
</nav>

<section class="hero" role="img" aria-label="Aerial photograph of a city skyline with a tall tower, harbour behind, at dusk">
  <h1 class="hero-title">KELTO CONSTRUCTION</h1>
  <p class="hero-sub">We are a mid to high-end construction company</p>
  <svg class="hero-arrows" width="88" height="40" viewBox="0 0 88 40"><path d="M22 4L8 20l14 16" fill="none" stroke="#fff" stroke-width="3"/><path d="M66 4l14 16-14 16" fill="none" stroke="#fff" stroke-width="3"/></svg>
</section>

<section class="welcome">
  <h2 class="section-title">WELCOME TO KELTO CONSTRUCTION</h2>
  <div class="rule"></div>
  <p class="lead">Aliquam molestie, mi et imperdiet euismod, dui purus auctor tellus, et interdum lacus lectus et ante. Sed accumsan sollicitudin sapien, sit amet adipiscing turpis<br>gravida ac. In congue, neque ac lobortis volutpat, libero mauris varius mi, vitae suscipit ipsum ligula vitae risus. Duis aliquam nibh a dui iaculis<br>viverra id a velit. Vivamus egestas risus in magna varius commodo.</p>
  <div class="btn">READ MORE</div>
</section>

<section class="services">
  <h2 class="section-title">OUR SERVICES</h2>
  <div class="rule"></div>
  <p class="lead">Aliquam molestie, mi et imperdiet euismod, dui purus auctor tellus, et interdum lacus lectus et ante. Sed accumsan sollicitudin sapien, sit amet adipiscing turpis<br>gravida ac. In congue, neque ac lobortis volutpat, libero mauris varius mi,</p>

  <div class="service-card" style="left:74px">
    <svg role="img" aria-label="Hard hat icon" width="64" height="64" viewBox="0 0 64 64">
      <path d="M12 44a20 20 0 0140 0z" fill="#1a5cc0"/>
      <rect x="28" y="20" width="8" height="14" rx="2" fill="#ececec"/>
      <rect x="29.5" y="18" width="5" height="14" rx="1.5" fill="#1a5cc0"/>
      <rect x="6" y="44" width="52" height="7" rx="3.5" fill="#1a5cc0"/>
    </svg>
    <div class="name">Contracting</div>
  </div>
  <div class="service-card featured" style="left:342px">
    <svg role="img" aria-label="Ruler and pencil icon" width="64" height="64" viewBox="0 0 64 64">
      <g transform="rotate(45 32 32)">
        <rect x="24" y="2" width="16" height="60" rx="2" fill="#fff"/>
        <path d="M24 12h7M24 20h5M24 28h7M24 36h5M24 44h7M24 52h5" stroke="#1a5cc0" stroke-width="2"/>
      </g>
      <g transform="rotate(-45 32 32)">
        <rect x="26" y="6" width="12" height="40" fill="#fff" stroke="#1a5cc0" stroke-width="2"/>
        <rect x="26" y="6" width="12" height="6" fill="#1a5cc0"/>
        <path d="M26 46h12l-6 11z" fill="#fff" stroke="#1a5cc0" stroke-width="2"/>
      </g>
    </svg>
    <div class="name">Designing</div>
  </div>
  <div class="service-card" style="left:610px">
    <svg role="img" aria-label="Speech bubbles icon" width="64" height="64" viewBox="0 0 64 64">
      <rect x="4" y="14" width="38" height="26" rx="5" fill="#1a5cc0"/>
      <path d="M12 40l0 12 12-12z" fill="#1a5cc0"/>
      <rect x="26" y="4" width="34" height="22" rx="5" fill="#1a5cc0" stroke="#ececec" stroke-width="3"/>
      <path d="M50 26l0 9-9-9z" fill="#1a5cc0"/>
      <circle cx="35" cy="15" r="2" fill="#fff"/><circle cx="43" cy="15" r="2" fill="#fff"/><circle cx="51" cy="15" r="2" fill="#fff"/>
      <path d="M12 24h20M12 31h14" stroke="#fff" stroke-width="2.5" stroke-linecap="round"/>
    </svg>
    <div class="name">Consultation</div>
  </div>
  <div class="service-card" style="left:880px">
    <svg role="img" aria-label="Wrench and hammer icon" width="64" height="64" viewBox="0 0 64 64">
      <g transform="rotate(-45 32 32)">
        <rect x="28" y="18" width="8" height="42" rx="3" fill="#1a5cc0"/>
        <circle cx="32" cy="13" r="11" fill="#1a5cc0"/>
        <rect x="28.5" y="0" width="7" height="12" fill="#ececec"/>
      </g>
      <g transform="rotate(45 32 32)">
        <rect x="28.5" y="14" width="7" height="46" rx="3" fill="#1a5cc0" stroke="#ececec" stroke-width="2"/>
        <rect x="18" y="4" width="28" height="11" rx="2" fill="#1a5cc0" stroke="#ececec" stroke-width="2"/>
      </g>
    </svg>
    <div class="name">Maintenance</div>
  </div>
</section>

<section class="projects">
  <h2 class="section-title">OUR RECENT PROJECTS</h2>
  <div class="rule"></div>
  <p class="lead">Aliquam molestie, mi et imperdiet euismod, dui purus auctor tellus, et interdum lacus lectus et ante. Sed accumsan sollicitudin sapien, sit amet adipiscing turpis<br>gravida ac. In congue, neque ac lobortis volutpat, libero mauris varius mi,</p>

  <div class="project-card" style="left:74px;top:236px"><div class="photo" role="img" aria-label="Glass office buildings under a blue sky" style="background:linear-gradient(90deg,rgba(40,60,90,.35),rgba(255,255,255,0) 40%,rgba(40,60,90,.3)),linear-gradient(180deg,#2f66b8 0%,#6f9bd4 35%,#a9c0d8 55%,#5c6f84 80%,#3c4652 100%)"></div><div class="label">IT BUILDINGS</div></div>
  <div class="project-card" style="left:434px;top:236px"><div class="photo" role="img" aria-label="Bright lobby with stone walls, sofas and potted plants" style="background:linear-gradient(90deg,#8a7658 0%,#c9b79c 25%,#ece7df 55%,#d8d2c8 80%,#9c8e72 100%)"></div><div class="label">INSTITUTIONS</div></div>
  <div class="project-card" style="left:792px;top:236px"><div class="photo" role="img" aria-label="Industrial factory hall with machinery" style="background:linear-gradient(180deg,#4a5663 0%,#8b96a0 25%,#3d4b58 55%,#5a6d3a 80%,#c9a72c 100%)"></div><div class="label">INDUSTRIES</div></div>
  <div class="project-card" style="left:74px;top:470px"><div class="photo" role="img" aria-label="Shopping centre towers lit up at night" style="background:linear-gradient(90deg,rgba(20,25,45,.4),rgba(0,0,0,0) 50%,rgba(20,25,45,.4)),linear-gradient(180deg,#6f8fb8 0%,#2c3a58 35%,#3d4860 60%,#d9a24a 85%,#7a5a2c 100%)"></div><div class="label">SHOPPING MALL</div></div>
  <div class="project-card" style="left:434px;top:470px"><div class="photo" role="img" aria-label="Open plan office with glass partitions" style="background:linear-gradient(90deg,#9a9a9a 0%,#e6e6e6 30%,#f2f2f2 60%,#bdbdbd 100%)"></div><div class="label">COMMERCIAL</div></div>
  <div class="project-card" style="left:792px;top:470px"><div class="photo" role="img" aria-label="White apartment buildings around a swimming pool" style="background:linear-gradient(180deg,#8fc3e8 0%,#d8e8f0 30%,#ecebe4 55%,#4f8c5a 75%,#6fb7c9 100%)"></div><div class="label">RESIDENTIAL</div></div>

  <div class="dots"><span></span><span></span><span></span></div>
</section>

<section class="blog">
  <h2 class="section-title">BLOG</h2>
  <div class="rule"></div>

  <article class="blog-card" style="left:74px">
    <div class="photo" role="img" aria-label="Modern building exterior with a paved courtyard" style="background:linear-gradient(180deg,#7fb0e0 0%,#b9d0e6 35%,#d3b58a 55%,#9a8a72 80%,#7c7260 100%)"><div class="date-badge">01<small>FEB</small></div></div>
    <p>Placerat vehicula id suspendisse lorem eget. Vel et gravida. Non a dapibus eget scelerisque quisque curabitur leo wisi pulvinar erat morbi.</p>
    <div class="btn">READ MORE</div>
  </article>
  <article class="blog-card" style="left:434px">
    <div class="photo" role="img" aria-label="Looking up at a modern glass and steel interior" style="background:linear-gradient(135deg,#d6b25a 0%,#9c8f78 30%,#6f7a86 55%,#4f6fa8 75%,#b84a2e 100%)"><div class="date-badge">01<small>FEB</small></div></div>
    <p>Placerat vehicula id suspendisse lorem eget. Vel et gravida. Non a dapibus eget scelerisque quisque curabitur leo wisi pulvinar erat morbi.</p>
    <div class="btn">READ MORE</div>
  </article>
  <article class="blog-card" style="left:792px">
    <div class="photo" role="img" aria-label="City towers at dusk across an empty plaza" style="background:linear-gradient(180deg,#2e3f7a 0%,#6a5a9a 25%,#c4687a 42%,#3b4560 60%,#23272f 100%)"><div class="date-badge">01<small>FEB</small></div></div>
    <p>Placerat vehicula id suspendisse lorem eget. Vel et gravida. Non a dapibus eget scelerisque quisque curabitur leo wisi pulvinar erat morbi.</p>
    <div class="btn">READ MORE</div>
  </article>
</section>

<footer class="site-footer">
  <div class="foot-brand">Kelto Construction</div>
  <p class="foot-about">Morbi et orci. Nulla quam a. Diam sapien eu a nisl dignissim. Vestibulum et sit arcu turpis commodo. Sem nec quis. Tortor mi dictum. Neque et amet euismod...</p>
  <div class="foot-more">Read more</div>

  <div class="foot-title" style="left:372px">Quick Links</div>
  <nav class="quick">
    <a style="left:372px;top:112px">Home</a>
    <a style="left:486px;top:112px">Blog</a>
    <a style="left:372px;top:145px">About</a>
    <a style="left:486px;top:145px">Contact Us</a>
    <a style="left:372px;top:179px">Projects</a>
  </nav>

  <div class="foot-title" style="left:636px">Contact Us</div>
  <div class="contact-row" style="top:110px"><span class="ring"><svg width="14" height="18" viewBox="0 0 14 18"><path d="M7 0a7 7 0 017 7c0 5-7 11-7 11S0 12 0 7a7 7 0 017-7z" fill="#f2c200"/><circle cx="7" cy="7" r="2.5" fill="#0c1526"/></svg></span><span>#123, Lorium ipsum,Dolor<br>Amit. Newzland.</span></div>
  <div class="contact-row" style="top:164px"><span class="ring"><svg width="16" height="12" viewBox="0 0 16 12"><rect width="16" height="12" rx="1" fill="#f2c200"/><path d="M1 1l7 6 7-6" fill="none" stroke="#0c1526" stroke-width="1.4"/></svg></span><span style="padding-top:6px">info@keltosite.example</span></div>
  <div class="contact-row" style="top:218px"><span class="ring"><svg width="16" height="16" viewBox="0 0 24 24"><path d="M6.6 10.8a15 15 0 006.6 6.6l2.2-2.2c.3-.3.7-.4 1-.2 1.1.4 2.3.6 3.6.6.6 0 1 .4 1 1V20c0 .6-.4 1-1 1A17 17 0 013 4c0-.6.4-1 1-1h3.5c.6 0 1 .4 1 1 0 1.3.2 2.5.6 3.6.1.3 0 .7-.2 1z" fill="#f2c200"/></svg></span><span style="padding-top:6px">1-800 555 0148</span></div>

  <div class="foot-title" style="left:946px">Follow Us</div>
  <div class="social" aria-label="Social profiles"><span></span><span></span><span></span><span></span></div>
  <div class="copy">© 2018. Company Name<br>All Right Reserved</div>
  <div class="mark">M1</div>
</footer>

</body>
</html>
```